Digital Marketing Agency Landing Page

At VELIM, we offer a comprehensive solution for solar companies' client acquisition needs in the rapidly growing industry. We handle end-to-end client acquisition, meaning we manage the entire lifecycle of capturing new clients—from initial lead generation to delivering the ready-to-buy homeowner. Our expertise in targeted advertising, data analytics, and customer relationship management ensures that we not only find potential customers but also nurture them through tailored engagement strategies until they are ready to make a purchase. By entrusting us with your client acquisition process, solar companies can focus on what they do best—providing sustainable energy solutions—while we work behind the scenes to grow your customer base and increase your market share.

We need to restructure our website to make it more professional. We don't need any complex functionalities. We are looking for someone that is good in design and can build a visually aesthetic website following our brand image. We only need a landing page and a lead form in the end. I would like to have only one page, but a relatively big one where people scroll down. I would like to have a minimal and classy look. Something that is timeless and elegant.

Structure:

initial page
About us
How we operate
Get in touch

Target Market(s)

Solar Comapanies

Industry/Entity Type

Marketing solautions

Coding

Coded - Design and coding required

Number of Pages Required

1 page

Requirements
Nice to have
• Inspirations: https://www.qz.zu/ https://www.marchbeck.example/ https://www.tovanrid.example/ https://pruvo.example/

```html
<!DOCTYPE html>
<html lang="en">
<head>
<meta charset="utf-8">
<title>VELIM — Client Acquisition for Solar Companies</title>
<link rel="stylesheet" href="https://fonts.googleapis.com/css2?family=Jost:wght@300;400;500;600&family=Didact+Gothic&display=swap">
<style>
:root{
  --navy:#13202e;
  --hero:#1f2250;
  --hero-deep:#1a1d44;
  --cream:#efe7d8;
  --ink:#13202e;
  --body:#3d4650;
  --muted:#8a9097;
  --white:#ffffff;
  --black:#000000;
  --footer-logo:#d9d9d9;
  --field-shadow:0 2px 8px rgba(0,0,0,.12);
}
*{box-sizing:border-box;margin:0;padding:0}
html,body{width:1200px;height:2412px;overflow:hidden;background:var(--white)}
body{position:relative;font-family:"Didact Gothic",sans-serif;color:var(--body)}

.site-header{position:absolute;left:0;top:0;width:1200px;height:77px;background:var(--navy)}
.brand{position:absolute;font-family:"Jost",sans-serif;font-weight:300;font-size:32px;line-height:1;letter-spacing:1px;color:var(--cream)}
.site-header .brand{left:128px;top:22px}
.nav{position:absolute;display:flex;font-family:"Jost",sans-serif;font-weight:600;font-size:16px;color:var(--white);letter-spacing:.2px}
.site-header .nav{top:28px;left:580px}
.nav a{color:inherit;text-decoration:none}
.nav a:nth-child(1){margin-right:48px}
.nav a:nth-child(2){margin-right:54px}
.nav a:nth-child(3){margin-right:58px}

.hero{position:absolute;left:0;top:77px;width:1200px;height:518px;background:linear-gradient(90deg,var(--hero-deep) 0%,var(--hero) 60%,#2a2458 100%)}
.hero-title{position:absolute;left:113px;top:83px;font-family:"Jost",sans-serif;font-weight:300;font-size:52px;color:var(--cream);letter-spacing:.5px}
.hero-visual{position:absolute;left:585px;top:55px;width:615px;height:463px;background:radial-gradient(ellipse at 60% 55%,#2f8f86 0%,#2b3d78 38%,#26285e 70%,rgba(31,34,80,0) 100%)}

.lead-form{position:absolute;left:128px;top:270px;width:457px;height:450px;background:var(--white);border-radius:8px;box-shadow:0 4px 18px rgba(0,0,0,.12)}
.field{position:absolute;left:22px;width:413px;height:59px;border-radius:7px;background:var(--white);box-shadow:var(--field-shadow);padding:18px 28px;font-size:19px;color:var(--muted)}
.field-name{top:32px}.field-email{top:109px}.field-phone{top:186px}
.field-message{top:263px;height:104px}
.btn{position:absolute;display:flex;align-items:center;justify-content:center;background:var(--navy);color:var(--white);font-family:"Jost",sans-serif;font-weight:600;border-radius:6px;box-shadow:0 2px 5px rgba(0,0,0,.25)}
.lead-form .btn{left:25px;top:385px;width:108px;height:38px;font-size:18px}

.about-visual{position:absolute;left:95px;top:815px;width:450px;height:325px;background:linear-gradient(160deg,#5e9ae0 0%,#2f6fc4 55%,#e6e8ee 100%);border-radius:4px;opacity:.9}
.about-title{position:absolute;left:621px;top:728px;font-family:"Jost",sans-serif;font-weight:300;font-size:52px;color:var(--ink)}
.about-text{position:absolute;left:620px;top:820px;width:466px;font-size:17.5px;line-height:30px;letter-spacing:.45px;text-align:justify;hyphens:manual;color:var(--body)}
.about .btn{left:618px;top:1125px;width:134px;height:37px;font-size:17px}

.services{position:absolute;left:0;top:1278px;width:1200px;height:832px;background:var(--navy)}
.services-title{position:absolute;left:0;width:1200px;top:108px;text-align:center;font-family:"Jost",sans-serif;font-weight:300;font-size:52px;color:var(--cream)}
.card{position:absolute;top:250px;width:310px;height:476px;background:var(--white);border-radius:6px;text-align:center}
.card:nth-of-type(1){left:117px}.card:nth-of-type(2){left:443px}.card:nth-of-type(3){left:769px}
.card svg{position:absolute;left:132px;top:22px}
.card h3{position:absolute;left:0;width:310px;top:88px;font-family:"Jost",sans-serif;font-weight:500;font-size:22px;letter-spacing:.6px;color:var(--ink)}
.card p{position:absolute;left:38px;width:234px;top:130px;font-size:17.5px;line-height:30px;letter-spacing:.3px;hyphens:manual;color:var(--body)}
.card .more{position:absolute;left:0;width:310px;top:420px;font-family:"Jost",sans-serif;font-weight:600;font-size:16px;color:var(--ink);text-decoration:underline;text-underline-offset:3px}

.site-footer{position:absolute;left:0;top:2110px;width:1200px;height:302px;background:var(--black)}
.site-footer .brand{left:0;width:1200px;top:70px;text-align:center;color:var(--footer-logo)}
.site-footer .nav{top:142px;left:344px}
.social{position:absolute;top:198px;left:0;width:1200px;display:flex;justify-content:center;gap:20px;font-size:13px;color:var(--white)}
.rule{position:absolute;left:111px;top:249px;width:973px;height:1px;background:#cfcfcf}
.copyright{position:absolute;left:115px;top:268px;font-size:15px;color:var(--white)}
</style>
</head>
<body>

<header class="site-header">
  <div class="brand">VELIM</div>
  <nav class="nav"><a href="#">HOME</a><a href="#">ABOUT US</a><a href="#">OUR SERVICES</a><a href="#">CONTACT US</a></nav>
</header>

<section class="hero">
  <h1 class="hero-title">WELCOME TO VELIM</h1>
  <div class="hero-visual" role="img" aria-label="Illustration of a laptop showing a marketing analytics dashboard with rising 3D bar charts"></div>
</section>

<form class="lead-form">
  <div class="field field-name">Name</div>
  <div class="field field-email">Email Address</div>
  <div class="field field-phone">Phone Number</div>
  <div class="field field-message">Message</div>
  <div class="btn">SUBMIT</div>
</form>

<section class="about">
  <div class="about-visual" role="img" aria-label="Illustration of two solar panel arrays on stands"></div>
  <h2 class="about-title">ABOUT US</h2>
  <p class="about-text">Sed ut perspiciatis unde omnis iste natus error sit vo&shy;luptatem accusantium doloremque laudantium, totam rem aperiam, eaque ipsa quae ab illo inventore veritatis et quasi architecto beatae vitae dicta sunt explicabo. Nemo enim ipsam voluptatem quia voluptas sit asperna&shy;tur aut odit aut fugit, sed quia consequuntur magni do&shy;lores eos qui ratione voluptatem sequi nesciunt. Neque porro quisquam est, qui dolorem ipsum quia dolor sit amet.</p>
  <div class="btn">READ MORE</div>
</section>

<section class="services">
  <h2 class="services-title">OUR SERVICES</h2>
  <article class="card">
    <svg width="46" height="46" viewBox="0 0 46 46" fill="none" stroke="#13202e" stroke-width="1.5"><circle cx="23" cy="23" r="20"/><circle cx="23" cy="23" r="13"/><circle cx="23" cy="23" r="5"/><path d="M23 0v8M23 38v8M0 23h8M38 23h8"/></svg>
    <h3>TARGETED ADVERTISING</h3>
    <p>Sed ut perspiciatis unde omnis iste natus error sit vo&shy;luptatem accusantium do&shy;loremque laudantium, totam rem aperiam, eaque ipsa quae ab illo inventore veritatis et quasi architecto beatae vitae dicta sunt ex&shy;plicabo.</p>
    <a class="more" href="#">READ MORE</a>
  </article>
  <article class="card">
    <svg width="46" height="46" viewBox="0 0 46 46" fill="none" stroke="#13202e" stroke-width="1.5"><rect x="3" y="30" width="6" height="14"/><rect x="13" y="24" width="6" height="20"/><rect x="23" y="18" width="6" height="26"/><rect x="33" y="10" width="6" height="34"/><path d="M4 22l10-7 10 3 16-14"/><circle cx="40" cy="4" r="2"/></svg>
    <h3>DATA ANALYTICS</h3>
    <p>Sed ut perspiciatis unde omnis iste natus error sit vo&shy;luptatem accusantium do&shy;loremque laudantium, totam rem aperiam, eaque ipsa quae ab illo inventore veritatis et quasi architecto beatae vitae dicta sunt ex&shy;plicabo.</p>
    <a class="more" href="#">READ MORE</a>
  </article>
  <article class="card">
    <svg width="46" height="46" viewBox="0 0 46 46" fill="none" stroke="#13202e" stroke-width="1.5"><circle cx="23" cy="6" r="4"/><path d="M16 20v-4a7 7 0 0 1 14 0v4"/><path d="M2 26l10-6 11 8 11-8 10 6"/><path d="M12 20l11 18 11-18"/></svg>
    <h3>CUSTOMER RELATIONSHIP</h3>
    <p>Sed ut perspiciatis unde omnis iste natus error sit vo&shy;luptatem accusantium do&shy;loremque laudantium, totam rem aperiam, eaque ipsa quae ab illo inventore veritatis et quasi architecto beatae vitae dicta sunt ex&shy;plicabo.</p>
    <a class="more" href="#">READ MORE</a>
  </article>
</section>

<footer class="site-footer">
  <div class="brand">VELIM</div>
  <nav class="nav"><a href="#">HOME</a><a href="#">ABOUT US</a><a href="#">OUR SERVICES</a><a href="#">CONTACT US</a></nav>
  <div class="social"><span>Chirpa</span><span>Facet</span><span>Lenso</span><span>Tikra</span><span>Vidora</span></div>
  <div class="rule"></div>
  <div class="copyright">© 2023 Velim</div>
</footer>

</body>
</html>
```